Tandem Hearth Works Pty Ltd

We need business cards for a company based in Perth, we install, service and maintain fire equipment.
On the front we want a great design with our logo and a small spot for our full company name, general company email address and office number. On the back we need space for our name, title, mobile number and email address on the back.

Target Market(s)

Facility managers and commercial/industrial building owners/occupiers.

Contact Information for Business Card

Font styles to use
Sans Serif

Requirements
Must have
• Please only submit 5 of your best samples.
Darker tones are preferred.
Nice to have
• We want to use, black, red and grey. Keep it modern and clean.
I've attached the company logo and a sample of a boarder we use on our emergency plans.
Should not have
• No preference. Let the designer choose.

```html
<!DOCTYPE html>
<html lang="en">
<head>
<meta charset="utf-8">
<title>Tandem Hearth Works – Business Card</title>
<link rel="stylesheet" href="https://fonts.googleapis.com/css2?family=Hind:wght@400;600;700&display=swap">
<style>
  :root {
    --stage: #eceeed;
    --card-grey: #bdbec0;
    --card-red: #d3222d;
    --brand-red: #ee2a33;
    --paper: #ffffff;
    --ink: #111111;
  }
  html, body {
    margin: 0;
    padding: 0;
    width: 1200px;
    height: 1200px;
    overflow: hidden;
    background: var(--stage);
    font-family: "Hind", "Segoe UI", sans-serif;
  }
  .canvas {
    position: relative;
    width: 1200px;
    height: 1200px;
  }
  .card {
    position: absolute;
    left: 247px;
    width: 711px;
    height: 405px;
    display: block;
  }
  .card--front { top: 146px; }
  .card--back  { top: 652px; }
  .card-bg--grey { fill: var(--card-grey); }
  .card-bg--red  { fill: var(--card-red); }
  .bubble { fill: var(--paper); }
  .brand-name {
    fill: var(--brand-red);
    font-weight: 700;
    font-size: 86px;
    letter-spacing: 1px;
  }
  .company-name {
    fill: var(--ink);
    font-weight: 600;
    font-size: 30px;
  }
  .contact-line {
    fill: var(--ink);
    font-weight: 400;
    font-size: 23px;
  }
  .icon-disc { fill: var(--ink); }
  .icon-glyph { fill: var(--paper); }
  .icon-stroke { fill: none; stroke: var(--ink); stroke-width: 1.4; }
  .person-name {
    fill: var(--ink);
    font-size: 34px;
    font-weight: 400;
  }
  .person-name .strong { font-weight: 700; }
  .designation {
    fill: var(--ink);
    font-size: 24px;
    font-weight: 400;
  }
  .back-contact {
    fill: var(--ink);
    font-size: 24px;
    font-weight: 400;
  }
</style>
</head>
<body>
<main class="canvas">

  <!-- Front of card -->
  <svg class="card card--front" viewBox="0 0 711 405" xmlns="http://www.w3.org/2000/svg">
    <rect class="card-bg--grey" width="711" height="405"/>
    <ellipse class="bubble" cx="142" cy="44" rx="153" ry="119"/>

    <text class="brand-name" x="55" y="108">THW</text>

    <text class="company-name" x="244" y="223">Tandem Hearth Works Pty Ltd</text>

    <g class="contact-icon contact-icon--home" transform="translate(255,280)">
      <circle class="icon-disc" r="11"/>
      <path class="icon-glyph" d="M-6 0 L0 -6 L6 0 L4 0 L4 5 L1 5 L1 1 L-1 1 L-1 5 L-4 5 L-4 0 Z"/>
    </g>
    <text class="contact-line" x="278" y="288">123 Street Name, Country Pincode.</text>

    <g class="contact-icon contact-icon--phone" transform="translate(255,307)">
      <circle class="icon-disc" r="11"/>
      <rect class="icon-glyph" x="-4" y="-7" width="8" height="14" rx="1.5"/>
      <rect class="icon-disc" x="-2.5" y="-5" width="5" height="6"/>
    </g>
    <text class="contact-line" x="278" y="315">Ph: +000 12345678</text>

    <g class="contact-icon contact-icon--mail" transform="translate(255,336)">
      <circle class="icon-disc" r="11"/>
      <rect class="icon-glyph" x="-7" y="-5" width="14" height="10"/>
      <path class="icon-stroke" d="M-7 -5 L0 1 L7 -5 M-7 5 L-2 0 M7 5 L2 0"/>
    </g>
    <text class="contact-line" x="278" y="343">email@hostname.com</text>
  </svg>

  <!-- Back of card -->
  <svg class="card card--back" viewBox="0 0 711 405" xmlns="http://www.w3.org/2000/svg">
    <rect class="card-bg--red" width="711" height="405"/>
    <ellipse class="bubble" cx="143" cy="42" rx="153" ry="119"/>
    <ellipse class="bubble" cx="550" cy="364" rx="196" ry="162"/>

    <text class="person-name" x="54" y="89">FIRST <tspan class="strong">NAME</tspan></text>
    <text class="designation" x="54" y="122">Designation</text>

    <text class="back-contact" x="416" y="272">123 Street Name, State,</text>
    <text class="back-contact" x="416" y="297">Country Pincode.</text>
    <text class="back-contact" x="416" y="330">+000 12345678</text>
    <text class="back-contact" x="416" y="364">email@hostname.com</text>
  </svg>

</main>
</body>
</html>
```